Road Construction Company needs business cards

We would like a new business card designed for our business.

We're a road construction company based in Qld, Australia.

Can the business card please have the following information on it.

Name: Warren Halbeck
Position: General Manager
Phone: 0472 915 348
Email: Warren.halbeck@tovrin.com.au
Address: 87 Marrow Ave, Pendlebay, QLD, 4023
Website: www.tovrin.com.au

Visually we'd like the card to be professional and simple.

Attached is our logo.

Our website is www.tovrin.com.au

Target Market(s)

Men aged 25-60

Contact Information for Business Card

As listed in project description

Font styles to use
Serif

Requirements
Must have
• Large logo on back of card

```html
<!DOCTYPE html>
<html lang="en">
<head>
<meta charset="utf-8">
<title>Tovrin Business Card</title>
<link rel="stylesheet" href="https://fonts.googleapis.com/css2?family=Tinos:wght@400;700&display=swap">
<style>
  :root {
    --navy: #0354a3;
    --sky: #33a4d8;
    --paper: #ffffff;
    --backdrop: #e6e6e6;
  }
  * { margin: 0; padding: 0; box-sizing: border-box; }
  html, body {
    width: 1200px; height: 1200px; overflow: hidden;
    background: var(--backdrop);
    font-family: "Tinos", "Times New Roman", serif;
  }
  .card {
    position: absolute; left: 265px; width: 689px; height: 394px; overflow: hidden;
  }
  .card--front { top: 172px; background: var(--paper); }
  .card--back { top: 644px; background: var(--navy); }

  .wordmark {
    position: absolute; left: 0; right: 0; text-align: center;
    font-weight: 700; font-size: 58px; letter-spacing: 6px; line-height: 1;
  }
  .card--front .wordmark { top: 38px; color: var(--navy); }
  .card--back .wordmark { top: 172px; color: var(--paper); }

  .holder { position: absolute; left: 57px; top: 138px; }
  .holder__name { font-size: 43px; color: var(--navy); line-height: 1; }
  .holder__role {
    font-size: 11.5px; letter-spacing: 1.2px; color: var(--sky);
    margin-top: 6px; margin-left: 2px;
  }
  .divider {
    position: absolute; left: 57px; top: 202px; width: 576px; height: 1.5px;
    background: var(--sky);
  }

  .contacts { position: absolute; left: 57px; top: 223px; list-style: none; }
  .contacts li {
    display: flex; align-items: center; height: 28px; margin-bottom: 9px;
    font-size: 19px; color: var(--sky);
  }
  .contacts li:nth-child(2) { margin-bottom: 10px; }
  .contacts svg { width: 28px; height: 28px; margin-right: 16px; flex: none; }

  .address {
    position: absolute; left: 470px; top: 226px;
    font-size: 19px; line-height: 22px; color: var(--sky); font-style: normal;
  }
  .wave { position: absolute; left: 0; top: 0; width: 689px; height: 394px; }
</style>
</head>
<body>

<section class="card card--front">
  <svg class="wave" viewBox="0 0 1110 634" preserveAspectRatio="none" aria-hidden="true">
    <path fill="var(--navy)" d="M0,553 H200 C350,545 550,600 730,606 C900,612 1020,570 1110,536 V634 H0Z"/>
    <path fill="var(--sky)" d="M435,561 C650,590 950,575 1110,468 V525 C1000,560 850,592 730,596 C620,596 520,577 435,561Z"/>
  </svg>

  <div class="wordmark">TOVRIN</div>

  <div class="holder">
    <h1 class="holder__name" style="font-weight:400">Warren Halbeck</h1>
    <p class="holder__role">GENERAL MANAGER</p>
  </div>
  <div class="divider"></div>

  <ul class="contacts">
    <li>
      <svg viewBox="0 0 28 28" aria-hidden="true">
        <circle cx="14" cy="14" r="14" fill="var(--navy)"/>
        <path fill="#fff" d="M9.5 7.5 l2.5 -0.5 1.5 3.5 -1.6 1.2 c0.8 1.8 2 3 3.8 3.9 l1.3 -1.6 3.4 1.6 -0.5 2.5 c-5.5 0.6 -10.8 -4.5 -10.4 -10.6z"/>
      </svg>
      0472 915 348
    </li>
    <li>
      <svg viewBox="0 0 28 28" aria-hidden="true">
        <circle cx="14" cy="14" r="14" fill="var(--navy)"/>
        <rect x="7" y="9" width="14" height="10" fill="none" stroke="#fff" stroke-width="1.6"/>
        <path d="M7 9 L14 15 L21 9 M7 19 L12 14 M21 19 L16 14" fill="none" stroke="#fff" stroke-width="1.4"/>
      </svg>
      Warren.halbeck@tovrin.com.au
    </li>
    <li>
      <svg viewBox="0 0 28 28" aria-hidden="true">
        <circle cx="14" cy="14" r="14" fill="var(--navy)"/>
        <circle cx="14" cy="14" r="7.5" fill="none" stroke="#fff" stroke-width="1.6"/>
        <path d="M6.5 14 H21.5 M14 6.5 C10.5 10 10.5 18 14 21.5 M14 6.5 C17.5 10 17.5 18 14 21.5" fill="none" stroke="#fff" stroke-width="1.2"/>
      </svg>
      www.tovrin.com.au
    </li>
  </ul>

  <address class="address">87 Marrow Ave,<br>Pendlebay, QLD, 4023</address>
</section>

<section class="card card--back">
  <div class="wordmark">TOVRIN</div>
</section>

</body>
</html>
```